New Locksmith Business needs a newspaper ad

We need an ad for a new locksmith business in Colorado called Riverbend Key Co. Our service area is located near several world-class ski resorts, which fuel the local economy. We are a comprehensive locksmith business offering automotive, commercial and residential services. We provide modern, tech-savvy digital security solutions for your home or business.

Size of ad: 3.22" x 3.44" | PDF needed for final artwork file

Target Market(s)

Local residents, businesses, hotels and resorts. As well as visitors to the area that may need emergency lock out services. High income, high net worth clients.

Industry/Entity Type

Locksmith

Font styles to use
Sans Serif

Requirements
Must have
• *Include: Logo
*Include: 970.318.2956
*Include: riverbendkeyco.com
*Include photo of Gus, he's the locksmith
*Include text: New Business!
*Include text: Auto | Residential | Commercial
*Include: Innovative Locksmith Solutions
*Colors from the logo are the main colors to use; accent color is Chrome Yellow (#ffac00)
*Bank Gothic is the headline font and we like to use Oswald font for all other text
Nice to have
• It would be nice to include another photo, in addition to the photo of Gus, if there is space. I know it is a small space, so no worries if adding another photo will not work.

```html
<!DOCTYPE html>
<html lang="en">
<head>
<meta charset="utf-8">
<title>Riverbend Key Co – New Business Ad</title>
<link rel="stylesheet" href="https://fonts.googleapis.com/css2?family=Michroma&family=Oswald:wght@400;500;600;700&display=swap">
<style>
  :root {
    --brand-blue: #337bc4;
    --bar-blue: #3a7cc6;
    --band-gray: #5b5b5b;
    --ring-gray: #a3a3a3;
    --paper: #ffffff;
    --stage: #eeeeee;
    --ink-light: #ffffff;
  }
  html, body {
    margin: 0;
    padding: 0;
    width: 864px;
    height: 1200px;
    overflow: hidden;
    background: var(--stage);
  }
  .ad {
    position: absolute;
    left: 0;
    top: 140px;
    width: 864px;
    height: 920px;
    display: block;
    box-shadow: 0 6px 22px rgba(0, 0, 0, 0.25);
  }
  .brand-name {
    font-family: "Oswald", sans-serif;
    font-weight: 600;
    font-size: 56px;
    fill: var(--brand-blue);
  }
  .headline {
    font-family: "Oswald", sans-serif;
    font-weight: 700;
    font-size: 112px;
    fill: var(--ink-light);
  }
  .services {
    font-family: "Oswald", sans-serif;
    font-weight: 600;
    font-size: 48px;
    fill: var(--ink-light);
  }
  .tagline {
    font-family: "Michroma", sans-serif;
    font-size: 21px;
    fill: var(--ink-light);
  }
  .phone-number {
    font-family: "Oswald", sans-serif;
    font-weight: 600;
    font-size: 66px;
    fill: var(--ink-light);
  }
  .web-address {
    font-family: "Oswald", sans-serif;
    font-weight: 400;
    font-size: 33px;
    fill: var(--ink-light);
  }
</style>
</head>
<body>
<svg class="ad" viewBox="0 0 878 935" xmlns="http://www.w3.org/2000/svg" aria-label="Riverbend Key Co newspaper advertisement">
  <defs>
    <linearGradient id="scene-tones" x1="0" y1="0" x2="0" y2="1">
      <stop offset="0" stop-color="#3f78bd"/>
      <stop offset="0.35" stop-color="#8aa9cb"/>
      <stop offset="0.5" stop-color="#5d6c7a"/>
      <stop offset="0.62" stop-color="#4a6a38"/>
      <stop offset="1" stop-color="#2d4624"/>
    </linearGradient>
    <linearGradient id="smart-lock-tones" x1="0" y1="0" x2="1" y2="1">
      <stop offset="0" stop-color="#c4855a"/>
      <stop offset="1" stop-color="#8e5a36"/>
    </linearGradient>
    <linearGradient id="keypad-tones" x1="0" y1="0" x2="1" y2="1">
      <stop offset="0" stop-color="#6a6a6a"/>
      <stop offset="1" stop-color="#262626"/>
    </linearGradient>
    <linearGradient id="portrait-tones" x1="0" y1="0" x2="0" y2="1">
      <stop offset="0" stop-color="#a07a52"/>
      <stop offset="0.7" stop-color="#d4a48a"/>
      <stop offset="1" stop-color="#2456b8"/>
    </linearGradient>
  </defs>

  <!-- mountain scenery backdrop -->
  <rect class="scenery" role="img" aria-label="Photo of a green ski-resort valley below rocky mountain peaks and a blue sky with clouds" x="0" y="0" width="878" height="935" fill="url(#scene-tones)"/>

  <!-- header waves -->
  <path class="wave-gray" d="M0 0 H878 V182 C780 175 700 200 600 235 C480 275 300 290 0 210 Z" fill="var(--band-gray)"/>
  <path class="wave-blue" d="M0 0 H878 V110 C760 110 660 160 560 210 C470 255 340 290 220 280 C130 272 60 240 0 205 Z" fill="var(--brand-blue)"/>
  <path class="header-paper" d="M0 0 H878 V95 C760 95 660 130 560 170 C450 215 330 245 230 235 C140 228 60 180 0 130 Z" fill="var(--paper)"/>

  <!-- brand -->
  <circle class="brand-dot" cx="140" cy="105" r="38" fill="var(--brand-blue)"/>
  <text class="brand-name" x="196" y="128">Riverbend Key Co</text>

  <!-- headline block -->
  <text class="headline" x="439" y="412" text-anchor="middle" textLength="630" lengthAdjust="spacingAndGlyphs">NEW BUSINESS!</text>
  <rect class="services-bar" x="84" y="435" width="720" height="60" rx="6" fill="var(--bar-blue)"/>
  <text class="services" x="444" y="484" text-anchor="middle" textLength="600" lengthAdjust="spacingAndGlyphs">AUTO | RESIDENTIAL | COMMERCIAL</text>
  <text class="tagline" x="444" y="550" text-anchor="middle" textLength="642" lengthAdjust="spacing">INNOVATIVE LOCKSMITH SOLUTIONS</text>

  <!-- footer waves -->
  <path class="footer-paper" d="M0 780 C200 760 350 790 520 760 C650 735 760 660 878 630 V935 H0 Z" fill="var(--paper)"/>
  <path class="footer-blue" d="M0 812 C200 802 380 822 540 792 C680 767 780 702 878 687 V935 H0 Z" fill="var(--brand-blue)"/>

  <!-- service photos -->
  <circle class="photo-keypad" role="img" aria-label="Photo of a hand holding a key card to a wall-mounted keypad reader" cx="359" cy="734" r="88" fill="url(#keypad-tones)"/>
  <circle class="photo-smart-lock" role="img" aria-label="Photo of a smartphone app controlling a smart door lock on a wooden door" cx="190" cy="714" r="112" fill="url(#smart-lock-tones)"/>

  <!-- locksmith portrait -->
  <circle class="portrait-ring" cx="687" cy="712" r="140" fill="var(--ring-gray)"/>
  <circle class="portrait" role="img" aria-label="Photo of Gus, the locksmith, smiling in a blue shirt" cx="687" cy="712" r="128" fill="url(#portrait-tones)"/>

  <!-- contact -->
  <g class="phone-icon" fill="none" stroke="var(--ink-light)">
    <circle cx="78" cy="875" r="29" stroke-width="5"/>
    <path d="M68 860 c-6 4 -6 12 0 22 c6 10 14 14 20 10 l3 -3 -7 -7 -4 3 c-3 -1 -8 -7 -9 -10 l3 -4 -6 -8 z" fill="var(--ink-light)" stroke="none"/>
  </g>
  <text class="phone-number" x="120" y="901" textLength="332" lengthAdjust="spacingAndGlyphs">970.318.2956</text>

  <g class="globe-icon" fill="none" stroke="var(--ink-light)" stroke-width="2.5">
    <circle cx="498" cy="883" r="12"/>
    <ellipse cx="498" cy="883" rx="5" ry="12"/>
    <line x1="486" y1="883" x2="510" y2="883"/>
  </g>
  <text class="web-address" x="518" y="895" textLength="326" lengthAdjust="spacingAndGlyphs">www.riverbendkeyco.com</text>
</svg>
</body>
</html>
```